Harbor Crestline (Business Card Design)

Need business cards designed. Something modern, chic, and sleek. Mabye the back of the card should be the navy blue that is in the logo and then just the logo on the back.

Target Market(s)

Those in the hotel, office, and renovation industry

Contact Information for Business Card

1. Logo 2. Dorian Fenwick 3. CEO/Founder 4. Phone: (833) HarbCre / (833) 427-2731 5. Email: dorian@theharborcrestline.com 6. Website: www.theharborcrestline.com

Font styles to use
Other font styles liked:
• Look at the logo font and base the font for everything else off of that.

Colors
0054AA
0677BA
7BADD7
CADEEF
E8F1F8

Requirements
Must have
• Colors that are associated in the logo
Nice to have
• Sleek modern clean and chic design.

```html
<!DOCTYPE html>
<html lang="en">
<head>
<meta charset="utf-8">
<title>Harbor Crestline — Business Card</title>
<link href="https://fonts.googleapis.com/css2?family=Montserrat:wght@500;600;700&family=Open+Sans:wght@400;600&display=swap" rel="stylesheet">
<style>
  :root {
    --navy: #0e1848;
    --navy-deep: #0a1236;
    --gold: #c9a03f;
    --white: #ffffff;
    --stage: #2a2a2e;
    --muted: rgba(255,255,255,0.08);
  }
  * { margin: 0; padding: 0; box-sizing: border-box; }
  html, body { width: 1200px; height: 780px; overflow: hidden; }
  body {
    background: var(--stage);
    font-family: "Open Sans", Arial, sans-serif;
    position: relative;
  }
  .card {
    position: absolute;
    top: 235px;
    width: 540px;
    height: 309px;
    background: var(--navy);
    border-radius: 22px;
    border: 2px solid var(--gold);
    overflow: hidden;
    color: var(--white);
  }
  .card--back { left: 40px; }
  .card--front { left: 620px; }

  .brand {
    display: flex;
    align-items: center;
    gap: 10px;
    font-family: "Montserrat", Arial, sans-serif;
    font-weight: 600;
    color: var(--white);
    letter-spacing: 0.12em;
    text-transform: uppercase;
    white-space: nowrap;
  }
  .brand__mark {
    width: 12px; height: 12px;
    background: var(--gold);
    flex: none;
  }
  .card--back .brand {
    position: absolute;
    left: 50%; top: 50%;
    transform: translate(-50%, -50%);
    font-size: 30px;
  }

  .corner-band {
    position: absolute;
    top: 0; right: 34px;
    width: 16px; height: 58px;
    background: var(--gold);
  }
  .person {
    position: absolute;
    top: 30px; right: 64px;
    text-align: right;
  }
  .person__name {
    font-family: "Montserrat", Arial, sans-serif;
    font-weight: 700;
    font-size: 28px;
    color: var(--gold);
    line-height: 1.05;
  }
  .person__role {
    font-family: "Montserrat", Arial, sans-serif;
    font-weight: 500;
    font-size: 13px;
    color: var(--white);
    margin-top: 4px;
    letter-spacing: 0.02em;
  }
  .decor-square {
    position: absolute;
    right: 46px; top: 104px;
    width: 118px; height: 118px;
    background: linear-gradient(180deg, rgba(190,190,230,0.35), rgba(10,18,54,0.6));
    box-shadow: 2px 3px 6px rgba(0,0,0,0.45);
  }
  .card--front .brand {
    position: absolute;
    left: 36px; top: 136px;
    font-size: 20px;
  }
  .brand__mark--small { width: 10px; height: 10px; }

  .contact {
    position: absolute;
    left: 36px; top: 178px;
    font-size: 12.5px;
    line-height: 1.42;
  }
  .contact__address { margin-bottom: 10px; }
  .contact__row {
    display: flex;
    align-items: center;
    gap: 8px;
  }
  .contact__icon { width: 13px; height: 13px; flex: none; }
</style>
</head>
<body>

  <section class="card card--back" aria-label="Card back">
    <div class="brand"><span class="brand__mark"></span>Harbor Crestline</div>
  </section>

  <section class="card card--front" aria-label="Card front">
    <div class="corner-band"></div>
    <div class="person">
      <div class="person__name">Dorian Fenwick</div>
      <div class="person__role">CEO/Founder</div>
    </div>
    <div class="decor-square"></div>

    <div class="brand"><span class="brand__mark brand__mark--small"></span>Harbor Crestline</div>

    <div class="contact">
      <p class="contact__address">4120 Larkmoor Ave<br>Suite 210, Easton, MD 21601</p>
      <p class="contact__row">
        <svg class="contact__icon" viewBox="0 0 24 24" aria-hidden="true"><path fill="#c9a03f" d="M6.6 10.8a15.1 15.1 0 0 0 6.6 6.6l2.2-2.2c.3-.3.7-.4 1-.2 1.1.4 2.3.6 3.6.6.6 0 1 .4 1 1V20c0 .6-.4 1-1 1A17 17 0 0 1 3 4c0-.6.4-1 1-1h3.5c.6 0 1 .4 1 1 0 1.3.2 2.5.6 3.6.1.3 0 .7-.2 1z"/></svg>
        (833) HarbCre / (833) 427-2731
      </p>
      <p class="contact__row">
        <svg class="contact__icon" viewBox="0 0 24 24" aria-hidden="true"><g fill="none" stroke="#c9a03f" stroke-width="2"><circle cx="12" cy="12" r="9"/><path d="M3 12h18M12 3c3 3 3 15 0 18M12 3c-3 3-3 15 0 18"/></g></svg>
        www.theharborcrestline.com
      </p>
      <p class="contact__row">
        <svg class="contact__icon" viewBox="0 0 24 24" aria-hidden="true"><g fill="none" stroke="#c9a03f" stroke-width="2"><rect x="3" y="5" width="18" height="14" rx="1"/><path d="M3 6l9 7 9-7"/></g></svg>
        dorian@theharborcrestline.com
      </p>
    </div>
  </section>

</body>
</html>
```